Redesign This Psychology Website

We would like a slight redesign of this successful psychology (relationship counselling) website:

www.TheKelvaleClinic.com.au

We are updating the website, and we'd like a slight refresh of the design and style.

Please keep to very similar colours, and use the same logo. We're looking for around 10 page templates, however the main one is the home page.

Keep in mind, this website already converts quite well, so we want a new, fresh design in keeping with this one. Please don't bother designing something too extremely different.

thanks :)

Target Market(s)

couples who are looking for relationship counselling. Men and women, 25 - 70, across Australia

Industry/Entity Type

Psychology

Number of Pages Required

5+ page

Font styles to use
Sans Serif

Colors
87cfc6
b7a5cd
ec1f27
ffffff
cee9f5

Requirements
Must have
• a similar look to the current design, just looking for a slight refresh.
• Search bar
• Areas for lots of photos
• same logo
• lots of content areas
Nice to have
• great content areas, where we can display a lot of content and our areas.
Should not have
• no colors like orange, etc.
• should not have a totally different feel.

```html
<!DOCTYPE html>
<html lang="en">
<head>
<meta charset="utf-8">
<title>The Kelvale Clinic – Relationship &amp; Marriage Counselling</title>
<link href="https://fonts.googleapis.com/css2?family=Questrial&family=Open+Sans:wght@400;600&display=swap" rel="stylesheet">
<style>
:root{
  --teal:#87cfc6;
  --teal-dark:#6fbdb3;
  --teal-text:#3aa9a0;
  --sky:#cee9f5;
  --red:#ec1f27;
  --ink:#444;
  --muted:#555;
  --topbar:#6b6b6b;
  --footer:#f2f2f2;
  --white:#fff;
}
*{box-sizing:border-box;margin:0;padding:0}
html,body{width:1200px;height:2416px;overflow:hidden;background:var(--white)}
body{font-family:"Open Sans",Arial,sans-serif;color:var(--ink);position:relative}
.heading{font-family:"Questrial","Century Gothic",sans-serif;font-weight:400}
.abs{position:absolute}
.btn{display:flex;align-items:center;justify-content:center;background:linear-gradient(#9edbd3,var(--teal-dark));color:var(--white);font-size:11px;text-transform:uppercase;border-radius:2px;box-shadow:0 1px 2px rgba(0,0,0,.15)}

/* top bar */
.topbar{left:0;top:0;width:1200px;height:35px;background:var(--topbar);color:#eee;font-size:11px;letter-spacing:.5px}
.topbar .call{left:132px;top:10px;display:flex;gap:8px;align-items:center}
.topbar .links{right:132px;top:10px;display:flex;gap:14px}
.topbar .links span.sep{opacity:.7}

/* header */
.header{left:0;top:35px;width:1200px;height:102px;background:var(--white)}
.brand{left:132px;top:28px;display:flex;align-items:center;gap:10px}
.brand .dot{width:38px;height:38px;border-radius:50%;background:var(--red)}
.brand .name{font-family:"Questrial",sans-serif;font-size:28px;color:var(--teal-text);line-height:1}
.search{left:864px;top:13px;width:204px;height:36px;background:#f1f1f1;font-size:11px;font-style:italic;color:#666;padding:11px 14px}
.search svg{position:absolute;right:12px;top:12px}
.nav{right:132px;top:70px;display:flex;gap:33px;font-size:11px;color:#555;text-transform:uppercase}
.nav .active{color:var(--teal-text)}

/* hero */
.hero{left:0;top:137px;width:1200px;height:472px;background:linear-gradient(100deg,#5a4a40 0%,#c9c6c2 40%,#eeeceb 60%,#e9a7bf 80%,#f2f2f2 100%)}
.hero-caption{left:0;top:84px;width:549px;height:279px;background:rgba(70,70,70,.72);color:var(--white)}
.hero-caption h1{position:absolute;left:166px;top:26px;font-size:30px;line-height:40px;letter-spacing:.5px;text-transform:uppercase}
.hero-caption p{position:absolute;left:166px;top:116px;font-size:18px;line-height:25px;text-transform:uppercase}
.hero-caption .btn{position:absolute;left:166px;top:188px;width:140px;height:45px;font-size:15px}
.dots{left:578px;top:440px;display:flex;gap:3px}
.dots i{width:12px;height:12px;border-radius:50%;background:#555;display:block}
.dots i:first-child{background:var(--teal)}

/* welcome */
.welcome h2{left:132px;top:664px;font-size:31px;color:#444}
.welcome .copy{left:132px;top:724px;width:450px;font-size:11px;line-height:20px;color:var(--muted);text-align:justify}
.welcome .copy p+p{margin-top:20px}
.welcome .btn{left:132px;top:920px;width:119px;height:37px}
.video{left:630px;top:677px;width:437px;height:280px;background:var(--white);box-shadow:0 1px 6px rgba(0,0,0,.35);padding:5px}
.video .still{width:100%;height:100%;background:linear-gradient(90deg,#e8eef2,#bcd9e6 45%,#d9e4ea)}
.video svg{position:absolute;left:225px;top:115px}

/* services */
.services{left:0;top:1031px;width:1200px;height:573px;background:var(--sky)}
.section-title{width:1200px;left:0;text-align:center;font-size:30px;color:#555}
.card{width:219px;height:382px;top:114px;background:var(--white);text-align:center}
.card .photo{height:170px}
.card h3{margin-top:22px;font-size:19px;color:#444;text-transform:uppercase}
.card p{margin:13px auto 0;width:184px;font-size:11px;line-height:19px;color:var(--muted)}
.card .btn{position:absolute;left:50px;top:323px;width:119px;height:32px}

/* blog */
.post{width:298px;top:1717px}
.post .photo{height:155px}
.post h3{margin-top:26px;width:280px;font-size:19px;line-height:25px;color:#444;text-transform:uppercase}
.post p{margin-top:11px;font-size:11px;line-height:19px;color:var(--muted)}
.post .more{margin-top:18px;font-size:11px;color:#444;text-transform:uppercase}

/* footer */
.footer{left:0;top:2112px;width:1200px;height:304px;background:var(--footer)}
.footer .brand{top:36px}
.social{left:132px;top:110px;display:flex;gap:9px}
.social i{width:30px;height:30px;border:1.5px solid #888;border-radius:50%;display:block}
.fcol h4{font-size:13px;font-weight:400;color:#444;text-transform:uppercase;margin-bottom:16px}
.fcol li{list-style:none;font-size:11px;color:#555;line-height:24px;text-transform:uppercase}
.fcol .note{font-size:10.5px;line-height:24px;color:#555;width:260px}
.fcol .field{margin-top:10px;width:252px;height:40px;background:var(--white);border:1px solid #ddd;border-radius:3px;font-size:11px;color:#666;padding:12px 14px}
.fcol .btn{margin-top:16px;width:82px;height:29px;font-size:10px}
.contact li{display:flex;gap:10px;text-transform:none;align-items:flex-start;margin-bottom:2px}
.contact svg{flex:none;margin-top:7px}
.rule{left:132px;top:2368px;width:936px;height:1px;background:#d6d6d6}
.copyright{left:0;width:1200px;top:2384px;text-align:center;font-size:10.5px;color:#555}
</style>
</head>
<body>

<div class="topbar abs">
  <div class="call abs">
    <svg width="11" height="11" viewBox="0 0 24 24"><path fill="#eee" d="M6.6 10.8a15 15 0 0 0 6.6 6.6l2.2-2.2c.3-.3.7-.4 1-.2 1.1.4 2.3.6 3.6.6.6 0 1 .4 1 1V20c0 .6-.4 1-1 1C10.6 21 3 13.4 3 4c0-.6.4-1 1-1h3.5c.6 0 1 .4 1 1 0 1.3.2 2.5.6 3.6.1.3 0 .7-.2 1z"/></svg>
    <span>CALL US ON: 1300 555 017</span>
  </div>
  <div class="links abs"><span>HOME</span><span class="sep">|</span><span>ABOUT RESOURCES</span><span class="sep">|</span><span>BLOG</span><span class="sep">|</span><span>SHOP</span></div>
</div>

<header class="header abs">
  <div class="brand abs">
    <span class="dot"></span>
    <div class="name">Kelvale Clinic</div>
  </div>
  <div class="search abs">Search...
    <svg width="11" height="11" viewBox="0 0 24 24"><circle cx="10" cy="10" r="7" fill="none" stroke="#555" stroke-width="3"/><path d="M15 15l7 7" stroke="#555" stroke-width="3"/></svg>
  </div>
  <nav class="nav abs"><span class="active">Counselling Types</span><span>Relationship Counselling</span><span>Sex Therapy</span><span>Quizzes</span><span>FAQ</span><span>Contact</span></nav>
</header>

<section class="hero abs" role="img" aria-label="Photo of a woman relaxing on a therapy couch while a counsellor listens">
  <div class="hero-caption abs">
    <h1 class="heading">Relationship &amp;<br>Marriage Counselling</h1>
    <p class="heading">At The Kelvale Clinic, we are a group<br>of psychologists</p>
    <div class="btn heading">Read More</div>
  </div>
  <div class="dots abs"><i></i><i></i><i></i></div>
</section>

<section class="welcome">
  <h2 class="heading abs">Welcome to The Kelvale Clinic</h2>
  <div class="copy abs">
    <p>At The Kelvale Clinic, we are a group of PSYCHOLOGISTS, Australia wide who are passionate about relationships and helping you with yours.</p>
    <p>Our vision is to provide the most highly regarded and comprehensive marriage counselling and relationship counselling, and sex therapy in Australia, at reasonable and affordable rates. When we are experiencing relationship and marriage problems, there can be a lot of pain and confusion, and it can often be difficult to cope with the other areas of our lives when we are struggling with problems with our partner.</p>
  </div>
  <div class="btn abs">Read More</div>
  <div class="video abs">
    <div class="still" role="img" aria-label="Video still of a psychologist introducing the clinic beside a couple in a session"></div>
    <svg width="60" height="42" viewBox="0 0 60 42"><rect width="60" height="42" rx="9" fill="#222" opacity=".85"/><path d="M24 12l14 9-14 9z" fill="#fff"/></svg>
  </div>
</section>

<section class="services abs">
  <h2 class="section-title heading abs" style="top:36px">Our Services</h2>
  <div class="card abs" style="left:132px">
    <div class="photo" role="img" aria-label="Photo of an upset couple sitting apart on the floor" style="background:linear-gradient(120deg,#d8cfc6,#8a9fb8)"></div>
    <h3 class="heading">Relationship</h3>
    <p>Communication, Recovering from an affair, Loss of intimacy &amp; love, Power battles, Feeling like friends, not lovers</p>
    <div class="btn">Read More</div>
  </div>
  <div class="card abs" style="left:371px">
    <div class="photo" role="img" aria-label="Photo of a couple lying apart in bed" style="background:linear-gradient(120deg,#b89c86,#f0ece8)"></div>
    <h3 class="heading">Sex Therapy</h3>
    <p>Communication, Recovering from an affair, Loss of intimacy &amp; love, Power battles, Feeling like friends, not lovers</p>
    <div class="btn">Read More</div>
  </div>
  <div class="card abs" style="left:610px">
    <div class="photo" role="img" aria-label="Photo of an angry man shouting at his laptop" style="background:linear-gradient(120deg,#e8e8e8,#6a6c74)"></div>
    <h3 class="heading">Anger</h3>
    <p>Communication, Recovering from an affair, Loss of intimacy &amp; love, Power battles, Feeling like friends, not lovers</p>
    <div class="btn">Read More</div>
  </div>
  <div class="card abs" style="left:849px">
    <div class="photo" role="img" aria-label="Photo of a frustrated woman with a man behind her" style="background:linear-gradient(120deg,#c9c3bd,#8a8a92)"></div>
    <h3 class="heading">Narcissism</h3>
    <p>Communication, Recovering from an affair, Loss of intimacy &amp; love, Power battles, Feeling like friends, not lovers</p>
    <div class="btn">Read More</div>
  </div>
</section>

<h2 class="section-title heading abs" style="top:1638px">Recent Blog</h2>
<article class="post abs" style="left:132px">
  <div class="photo" role="img" aria-label="Photo of a stressed woman covering her ears during an argument" style="background:linear-gradient(100deg,#c9b6a2,#6e6f58 55%,#4d4a47)"></div>
  <h3 class="heading">What can I do if I'm living with a narcissist?</h3>
  <p>If you are in a relationship with a Narcissist, in his/her mind, you are an extension of him/her and he/she must always win, so his/her eruptions of temper</p>
  <div class="more">Read More &raquo;</div>
</article>
<article class="post abs" style="left:451px">
  <div class="photo" role="img" aria-label="Photo of a worried woman with her partner in the background" style="background:linear-gradient(100deg,#8f8a86,#d8d4ce 55%,#b7b2aa)"></div>
  <h3 class="heading">What can I do if I'm living with a narcissist?</h3>
  <p>If you are in a relationship with a Narcissist, in his/her mind, you are an extension of him/her and he/she must always win, so his/her eruptions of temper</p>
  <div class="more">Read More &raquo;</div>
</article>
<article class="post abs" style="left:770px">
  <div class="photo" role="img" aria-label="Photo of an upset woman while a man gestures at her" style="background:linear-gradient(100deg,#a5a0a4,#7a5e58 40%,#c9c0b8)"></div>
  <h3 class="heading">What can I do if I'm living with a narcissist?</h3>
  <p>If you are in a relationship with a Narcissist, in his/her mind, you are an extension of him/her and he/she must always win, so his/her eruptions of temper</p>
  <div class="more">Read More &raquo;</div>
</article>

<footer class="footer abs">
  <div class="brand abs">
    <span class="dot"></span>
    <div class="name">Kelvale Clinic</div>
  </div>
  <div class="social abs"><i></i><i></i><i></i><i></i><i></i></div>

  <div class="fcol abs" style="left:424px;top:36px">
    <h4 class="heading">Quick Links</h4>
    <ul><li>Home</li><li>About</li><li>Resources Blog</li><li>Shop</li><li>Cart</li></ul>
  </div>

  <div class="fcol abs" style="left:596px;top:36px">
    <h4 class="heading">Newsletter</h4>
    <p class="note" style="padding-left:2px">Enter your email address to receive the latest news and notes from our blog.</p>
    <div class="field">Enter Your Mail Id</div>
    <div class="btn">Subscribe</div>
  </div>

  <div class="fcol contact abs" style="left:905px;top:36px">
    <h4 class="heading">Contact Us</h4>
    <ul>
      <li><svg width="10" height="10" viewBox="0 0 24 24"><path fill="#555" d="M6.6 10.8a15 15 0 0 0 6.6 6.6l2.2-2.2c.3-.3.7-.4 1-.2 1.1.4 2.3.6 3.6.6.6 0 1 .4 1 1V20c0 .6-.4 1-1 1C10.6 21 3 13.4 3 4c0-.6.4-1 1-1h3.5c.6 0 1 .4 1 1 0 1.3.2 2.5.6 3.6.1.3 0 .7-.2 1z"/></svg>(02) 5550 1472</li>
      <li><svg width="10" height="10" viewBox="0 0 24 24"><rect x="2" y="8" width="20" height="10" rx="2" fill="#555"/><rect x="6" y="3" width="12" height="6" fill="#555"/><rect x="6" y="15" width="12" height="6" fill="#555"/></svg>(02) 5550 1472</li>
      <li><svg width="10" height="10" viewBox="0 0 24 24"><rect x="2" y="5" width="20" height="14" fill="#555"/><path d="M2 5l10 8 10-8" fill="none" stroke="#fff" stroke-width="2"/></svg><span style="text-decoration:underline">hello@kelvaleclinic.com.au</span></li>
      <li style="line-height:18px"><svg width="10" height="12" viewBox="0 0 20 24"><path fill="#555" d="M10 0a8 8 0 0 0-8 8c0 6 8 16 8 16s8-10 8-16a8 8 0 0 0-8-8zm0 11a3 3 0 1 1 0-6 3 3 0 0 1 0 6z"/></svg><span style="margin-top:3px">#2868 Lorem ipsum dolor sit<br>amet, consectetur</span></li>
    </ul>
  </div>
</footer>
<div class="rule abs"></div>
<div class="copyright abs">©2017 The Kelvale Clinic. All rights reserved.</div>

</body>
</html>
```